need corporate, modern business card created for Consulting Company

I need a slick business card using elements from my website, as well as, integrating my pixelforge-created logo (see files).

The business card needs to be:
1. Corporate and modern
2. Clean and professional

I've included a PSD with the logo/icon that you can use to create it. Feel free to try a metallic finish on the logo, make it bigger/small, underlay it. Whatever you need to do to make my card stand out.

Try a black background, or white background or gray.

The idea is for my card to be memorable as well as professional and corporate.

Target Market(s)

Corporate business in the US and Canada.

Industry/Entity Type

Business

Contact Information for Business Card

Commerce Advancing Methods
Martin Coles, Senior Partner
office: 1 877 555 0143
mobile: 1 519 555 0172
website: http://www.brightvale.example

Requirements
Must have
• Card-related information
• corporate, yet modern
• clean and professional
• incorporate the icon only
• must have an editable form when complete!
Nice to have
• metallic icon might be cool
• try it with white or black

```html
<!DOCTYPE html>
<html lang="en">
<head>
<meta charset="utf-8">
<title>brightvale – business card</title>
<link rel="stylesheet" href="https://fonts.googleapis.com/css2?family=Open+Sans:ital,wght@0,400;0,600;0,700;1,400;1,600&display=swap">
<style>
  :root {
    --backdrop: #8d8f91;
    --card: #1f1f20;
    --brand-blue: #3b6fc6;
    --blue-deep: #2a56a3;
    --silver: #b9bcc0;
    --silver-dark: #6f7277;
    --ink-light: #f2f2f2;
    --ink-muted: #c9c9c9;
  }
  * { margin: 0; padding: 0; box-sizing: border-box; }
  html, body { width: 1200px; height: 772px; overflow: hidden; }
  body {
    background: var(--backdrop);
    font-family: "Open Sans", Arial, sans-serif;
    display: flex;
    align-items: center;
    justify-content: center;
    gap: 48px;
  }
  .card {
    position: relative;
    width: 540px;
    height: 309px;
    background: var(--card);
    border-radius: 4px;
    box-shadow: 0 10px 24px rgba(0,0,0,0.35);
    overflow: hidden;
    color: var(--ink-light);
  }
  .brand {
    display: flex;
    align-items: center;
    gap: 12px;
    color: var(--brand-blue);
    font-weight: 600;
    letter-spacing: -0.5px;
  }
  .brand-square {
    background: var(--brand-blue);
    border-radius: 2px;
  }
  .card-front { display: flex; align-items: center; justify-content: center; }
  .card-front .brand { font-size: 58px; }
  .card-front .brand-square { width: 44px; height: 44px; }

  .card-back .brand { position: absolute; left: 36px; top: 34px; font-size: 30px; gap: 9px; }
  .card-back .brand-square { width: 22px; height: 22px; }
  .address {
    position: absolute; left: 38px; top: 92px;
    font-size: 12px; font-style: italic; line-height: 1.45; color: var(--ink-muted);
  }
  .person { position: absolute; right: 34px; top: 38px; text-align: right; }
  .person-name { font-size: 15px; font-weight: 700; }
  .person-title { font-size: 14px; font-style: italic; color: var(--ink-muted); }
  .contacts {
    position: absolute; right: 34px; top: 118px; text-align: right;
    list-style: none; font-size: 12.5px; line-height: 1.55; color: var(--ink-muted);
  }
  .contacts li { display: flex; align-items: center; justify-content: flex-end; gap: 6px; }
  .contacts svg { width: 11px; height: 11px; fill: var(--ink-muted); }
  .swoosh { position: absolute; left: 0; bottom: 0; width: 540px; height: 309px; }
  .website {
    position: absolute; left: 40px; bottom: 34px;
    font-size: 12px; font-style: italic; color: var(--ink-light); letter-spacing: 0.3px;
  }
</style>
</head>
<body>
  <section class="card card-front">
    <div class="brand"><span class="brand-square"></span>brightvale</div>
  </section>

  <section class="card card-back">
    <svg class="swoosh" viewBox="0 0 540 309" aria-hidden="true">
      <defs>
        <linearGradient id="silver-band" x1="0" x2="1" y1="0" y2="0">
          <stop offset="0" stop-color="var(--silver-dark)"/>
          <stop offset="0.5" stop-color="var(--silver)"/>
          <stop offset="1" stop-color="var(--silver-dark)"/>
        </linearGradient>
      </defs>
      <path d="M0,196 C170,176 360,236 540,214 L540,246 C360,262 170,214 0,236 Z" fill="url(#silver-band)"/>
      <path d="M0,232 C170,212 360,258 540,244 L540,286 C360,300 170,262 0,282 Z" fill="var(--brand-blue)"/>
      <path d="M0,276 C170,258 360,296 540,282 L540,309 L0,309 Z" fill="var(--blue-deep)" opacity="0.35"/>
    </svg>

    <div class="brand"><span class="brand-square"></span>brightvale</div>

    <p class="address">214, 9th floor,<br>Harbor Point<br>Road NKV</p>

    <div class="person">
      <p class="person-name">Dana Whitlock</p>
      <p class="person-title">Consultant</p>
    </div>

    <ul class="contacts">
      <li>012 555 0199
        <svg viewBox="0 0 24 24"><path d="M6.6 10.8a15 15 0 0 0 6.6 6.6l2.2-2.2a1 1 0 0 1 1-.25 11.4 11.4 0 0 0 3.6.57 1 1 0 0 1 1 1V20a1 1 0 0 1-1 1A17 17 0 0 1 3 4a1 1 0 0 1 1-1h3.5a1 1 0 0 1 1 1c0 1.25.2 2.45.57 3.57a1 1 0 0 1-.25 1z"/></svg>
      </li>
      <li>012 555 0199
        <svg viewBox="0 0 24 24"><rect x="6" y="2" width="12" height="20" rx="2"/></svg>
      </li>
      <li>name@brightvale.example
        <svg viewBox="0 0 24 24"><path d="M2 5h20v14H2z M2 5l10 8 10-8" /></svg>
      </li>
    </ul>

    <p class="website">www.brightvale.example</p>
  </section>
</body>
</html>
```